Commercial and Residential Paint Contractor needs website

We need a website for our residential painting, multi-family painting and commercial painting company. We paint interior and exterior of houses, apartments and commercial buildings. I would like an about us page, residential page, multi family page, commercial page and contact us. Need keywords added to website for seo opitimazation. I like this website https://www.wallcraftcrew.com/

Target Market(s)

General Contractors and commercial property managers

Coding

Coded - Design and coding required

Number of Pages Required

5+ page

Font styles to use
Sans Serif

Requirements
Must have
• I need SEO keywords on pages

```html
<!DOCTYPE html>
<html lang="en">
<head>
<meta charset="utf-8">
<title>Crestline Painting | Residential, Multi-Family &amp; Commercial Painting Contractor</title>
<meta name="description" content="Crestline Painting – interior and exterior residential, multi-family and commercial painting contractor for general contractors and property managers.">
<link href="https://fonts.googleapis.com/css2?family=Montserrat:wght@400;500;600&family=Roboto:wght@400;500;700;900&display=swap" rel="stylesheet">
<style>
:root{
  --red:#c8202f;
  --ink:#1b1b1b;
  --text:#4a4a4a;
  --muted:#7d7d7d;
  --paper:#dedede;
  --card:#ffffff;
  --line:#9a9a9a;
  --black:#0e0e0e;
}
*{margin:0;padding:0;box-sizing:border-box}
html,body{width:1200px;height:4077px;overflow:hidden}
body{position:relative;background:var(--paper);font-family:"Montserrat",sans-serif;color:var(--text)}
.abs{position:absolute}
.photo{position:absolute}
.red{color:var(--red)}

/* header */
.logo{left:114px;top:18px;font-family:"Roboto",sans-serif;font-weight:900;font-size:30px;line-height:30px;color:var(--ink);letter-spacing:1px;display:flex;align-items:center;gap:10px}
.logo-mark{width:16px;height:16px;background:var(--red)}
.logo small{display:block;font-size:13px;letter-spacing:4px;line-height:16px}
.nav{left:0;top:36px;width:1200px;font-family:"Roboto",sans-serif;font-size:14px;color:var(--ink)}
.nav a{position:absolute;text-decoration:none;color:inherit;white-space:nowrap;transform:translateX(-50%)}
.nav a.active{color:#fff}
.nav a.active::after{content:"";position:absolute;left:0;right:0;bottom:-8px;height:3px;background:#fff}
.nav a.contact{transform:none;left:966px;top:-8px;width:118px;height:35px;line-height:35px;text-align:center;background:var(--black);color:#fff}

.hero{left:0;top:0;width:1200px;height:649px;background:linear-gradient(90deg,#d9731f 0%,#e07a22 50%,#ececec 53%,#e6e6e6 100%)}
.hero-title{left:701px;top:186px;font-family:"Roboto",sans-serif;font-weight:900;font-size:70px;line-height:66px;color:var(--ink)}
.hero-copy{left:707px;top:336px;width:300px;font-size:15px;line-height:25px;color:var(--ink)}
.btn{position:absolute;display:block;text-align:center;color:#fff;font-family:"Montserrat",sans-serif;font-weight:500;font-size:14px;letter-spacing:.5px;text-decoration:none}
.btn-dark{background:var(--black);left:703px;top:404px;width:139px;height:36px;line-height:36px}
.btn-red{background:var(--red);width:140px;height:38px;line-height:38px}

.roller{left:70px;top:586px;width:112px;height:152px;background:linear-gradient(180deg,#8f8f8f,#e9e9e9);border-radius:0 0 28px 28px}

/* sections */
.h2{font-family:"Roboto",sans-serif;font-weight:500;font-size:36px;line-height:40px;color:var(--ink);white-space:nowrap}
.center{text-align:center}
.sub{font-size:18px;line-height:24px;color:var(--ink);letter-spacing:.3px}
.para{font-size:15px;line-height:24px;color:var(--text)}
.svc-title{font-family:"Roboto",sans-serif;font-weight:400;font-size:28px;line-height:34px;color:var(--ink);text-align:center}

/* values */
.card{position:absolute;top:2811px;width:308px;height:342px;background:var(--card);text-align:center}
.card svg{position:absolute;left:50%;top:40px;transform:translateX(-50%)}
.card h3{position:absolute;top:152px;left:0;width:100%;font-family:"Roboto",sans-serif;font-weight:400;font-size:25px;letter-spacing:1.5px;color:var(--ink)}
.card p{position:absolute;top:207px;left:28px;right:28px;font-size:14.5px;line-height:26px;color:var(--text)}

/* contact */
.form-card{left:199px;top:3369px;width:428px;height:501px;background:var(--card)}
.form-card h4{position:absolute;left:32px;top:48px;font-family:"Montserrat",sans-serif;font-weight:600;font-size:18px;color:var(--ink)}
.field{position:absolute;left:32px;width:344px;border-bottom:1px solid var(--line);font-size:13px;color:var(--muted);padding-bottom:8px}
.rule{position:absolute;left:32px;width:344px;height:1px;background:var(--line)}
.form-btn{position:absolute;left:0;bottom:0;width:100%;height:63px;line-height:63px;background:var(--red);color:#fff;text-align:center;font-size:14px;font-weight:500}
.info-h{font-family:"Montserrat",sans-serif;font-weight:600;font-size:18px;color:var(--ink)}
.info-t{font-size:15px;line-height:26px;color:var(--muted)}

/* footer */
.footer{left:0;top:3958px;width:1200px;height:119px;background:var(--black)}
.foot-nav a{position:absolute;top:4000px;transform:translateX(-50%);color:#fff;font-family:"Roboto",sans-serif;font-weight:500;font-size:15px;letter-spacing:.8px;text-decoration:none;white-space:nowrap}
.copy{left:0;top:4047px;width:1200px;text-align:center;color:#fff;font-size:11px}
.roller-foot{left:1014px;top:3871px;width:186px;height:160px;background:linear-gradient(180deg,#f2f2f2,#8c8c8c);border-radius:40px 0 0 40px}
</style>
</head>
<body>

<header>
  <div class="photo hero" role="img" aria-label="Bedroom half painted orange and half white, with bed, framed art and window"></div>
  <div class="abs logo"><span class="logo-mark"></span><span>CRESTLINE<small>PAINTING</small></span></div>
  <nav class="abs nav">
    <a class="active" href="#home" style="left:366px">Home</a>
    <a href="#about" style="left:462px">About Us</a>
    <a href="#services" style="left:567px">Services</a>
    <a href="#customers" style="left:676px">Customers</a>
    <a href="#testimonials" style="left:798px">Testimonials</a>
    <a href="#news" style="left:904px">News</a>
    <a class="contact" href="#contact">Contact Us</a>
  </nav>
  <h1 class="abs hero-title">Crestline<br>Painting</h1>
  <p class="abs hero-copy">Consectetur adipiscing elit sed do eiusmod tempor incididunt ut laboreet</p>
  <a class="btn btn-dark" href="#contact">GET STARTED</a>
  <div class="photo roller" role="img" aria-label="Hand holding a paint roller"></div>
</header>

<section id="about">
  <h2 class="abs h2" style="left:111px;top:824px">ABOUT <span class="red">US</span></h2>
  <p class="abs sub" style="left:111px;top:875px">Consectetur adipiscing elit sed do eiusmod</p>
  <p class="abs para" style="left:111px;top:926px;width:390px">At vero eos et accusamus et iusto odio dignissimos ducimus qui blanditiis praesentium voluptatum deleniti atque corrupti quos dolores et quas molestias excepturi sint occaecati cupiditate non provident, similique sunmollitiet.</p>
  <a class="btn btn-red" href="#about" style="left:116px;top:1091px">READ MORE</a>
  <div class="photo" role="img" aria-label="Woman painting a wall teal with a roller among moving boxes" style="left:538px;top:738px;width:662px;height:441px;background:linear-gradient(90deg,#d7b98a 0%,#3f7f8c 35%,#e8e6e2 70%,#d9bf93 100%)"></div>
</section>

<section id="services">
  <h2 class="abs h2 center" style="left:0;top:1288px;width:1200px">OUR <span class="red">SERVICES</span></h2>
  <p class="abs sub center" style="left:0;top:1338px;width:1200px">Consectetur adipiscing elit sed do eiusmod</p>

  <div class="photo" role="img" aria-label="Freshly painted grey and red interior with ladder and paint supplies" style="left:111px;top:1388px;width:560px;height:342px;background:linear-gradient(90deg,#d9d6d2 0%,#b9b9bd 45%,#f1f1f1 65%,#8f1f22 90%)"></div>
  <h3 class="abs svc-title" style="left:714px;top:1417px;width:360px">RESIDENTIAL PAINTING</h3>
  <p class="abs para center" style="left:744px;top:1463px;width:300px">At vero eos et accusamus et iusto odio dignissimos ducimus qui blanditiis praesentium voluptatum deleniti atque corrupti quos dolores et quas molestias excepturi sint occaecati cupiditate non provident, similique sunt in culpa qui officia deserunt mollitia animi fuga.</p>
  <a class="btn btn-red" href="#residential" style="left:826px;top:1657px">READ MORE</a>

  <h3 class="abs svc-title" style="left:121px;top:1845px;width:360px">MULTI-FAMILY PAINTING</h3>
  <p class="abs para center" style="left:151px;top:1891px;width:300px">At vero eos et accusamus et iusto odio dignissimos ducimus qui blanditiis praesentium voluptatum deleniti atque corrupti quos dolores et quas molestias excepturi sint occaecati cupiditate non provident, similique sunt in culpa qui officia deserunt mollitia animi fuga.</p>
  <a class="btn btn-red" href="#multi-family" style="left:236px;top:2084px">READ MORE</a>
  <div class="photo" role="img" aria-label="Family painting an apartment wall turquoise beside a ladder" style="left:527px;top:1816px;width:561px;height:342px;background:linear-gradient(90deg,#c9c9c7 0%,#d8d8d6 40%,#5fb7bf 75%,#d4d4d2 100%)"></div>

  <div class="photo" role="img" aria-label="Two painters in safety gear painting a commercial building facade" style="left:111px;top:2245px;width:560px;height:342px;background:linear-gradient(90deg,#5f6e82 0%,#9aa3b0 50%,#e1e3e6 80%,#b9bcc0 100%)"></div>
  <h3 class="abs svc-title" style="left:714px;top:2258px;width:360px">COMMERCIAL PAINTING<br>COMPANY</h3>
  <p class="abs para center" style="left:744px;top:2337px;width:300px">At vero eos et accusamus et iusto odio dignissimos ducimus qui blanditiis praesentium voluptatum deleniti atque corrupti quos dolores et quas molestias excepturi sint occaecati cupiditate non provident, similique sunt in culpa qui officia deserunt mollitia animi fuga.</p>
  <a class="btn btn-red" href="#commercial" style="left:826px;top:2527px">READ MORE</a>
</section>

<section id="values">
  <h2 class="abs h2 center" style="left:0;top:2693px;width:1200px">WHAT <span class="red">CRESTLINE PAINTING</span> VALUES</h2>
  <p class="abs sub center" style="left:0;top:2742px;width:1200px">Consectetur adipiscing elit sed do eiusmod</p>

  <div class="card" style="left:111px">
    <svg width="84" height="84" viewBox="0 0 84 84" fill="none" stroke="#c8202f" stroke-width="2.5" aria-hidden="true">
      <path d="M14 44 C14 22 28 12 42 12 C56 12 70 22 70 44"/><path d="M8 44h68v6H8z"/><path d="M34 12v20M50 12v20"/>
      <rect x="14" y="58" width="56" height="16" rx="6"/><path d="M42 58v16"/>
    </svg>
    <h3>YOUR SAFETY</h3>
    <p>At vero eos et accusamus et iusto odio dignissimos ducimus qui blanditiis praesentium voluptatum deleniti atque.</p>
  </div>
  <div class="card" style="left:445px">
    <svg width="84" height="84" viewBox="0 0 84 84" fill="none" stroke="#c8202f" stroke-width="2.5" aria-hidden="true">
      <circle cx="46" cy="46" r="28"/><path d="M40 10h12M46 10v8M34 46l9 9 16-18"/><path d="M4 40h12M2 48h12M6 56h12"/>
    </svg>
    <h3>YOUR TIME</h3>
    <p>At vero eos et accusamus et iusto odio dignissimos ducimus qui blanditiis praesentium voluptatum deleniti atque.</p>
  </div>
  <div class="card" style="left:780px">
    <svg width="84" height="84" viewBox="0 0 84 84" fill="none" stroke="#c8202f" stroke-width="2.5" aria-hidden="true">
      <circle cx="42" cy="42" r="34"/><circle cx="42" cy="42" r="24"/><circle cx="42" cy="36" r="7"/><path d="M30 58c2-8 7-11 12-11s10 3 12 11"/>
    </svg>
    <h3>YOUR EXPERIENCE</h3>
    <p>At vero eos et accusamus et iusto odio dignissimos ducimus qui blanditiis praesentium voluptatum deleniti atque.</p>
  </div>
</section>

<section id="contact">
  <h2 class="abs h2 center" style="left:0;top:3261px;width:1200px">CONTACT <span class="red">US</span></h2>
  <p class="abs sub center" style="left:0;top:3311px;width:1200px">Nam libero temporeum soluta nobis</p>

  <form class="abs form-card">
    <h4>Send Us A Message</h4>
    <div class="field" style="top:106px">Full Name</div>
    <div class="field" style="top:174px">Email</div>
    <div class="field" style="top:242px">Write A Message</div>
    <div class="rule" style="top:319px"></div>
    <div class="rule" style="top:367px"></div>
    <div class="form-btn">READ MORE</div>
  </form>

  <p class="abs info-h" style="left:708px;top:3447px">Address</p>
  <p class="abs info-t" style="left:708px;top:3485px;width:300px">418 Alder Ridge Road, Fairmont, Nebraska, 68354, USA</p>
  <p class="abs info-h" style="left:708px;top:3572px">Call Us</p>
  <p class="abs info-t" style="left:708px;top:3609px">555 204 7731<br>555 318 6042</p>
  <p class="abs info-h" style="left:708px;top:3697px">Mail Us</p>
  <p class="abs info-t" style="left:708px;top:3734px">hello@crestlinepainting.example</p>
</section>

<footer>
  <div class="abs footer"></div>
  <div class="photo roller-foot" role="img" aria-label="Hand holding a paint roller"></div>
  <nav class="foot-nav">
    <a href="#home" style="left:275px">Home</a>
    <a href="#about" style="left:391px">About Us</a>
    <a href="#services" style="left:518px">Services</a>
    <a href="#customers" style="left:651px">Customers</a>
    <a href="#testimonials" style="left:798px">Testimonials</a>
    <a href="#news" style="left:926px">News</a>
  </nav>
  <p class="abs copy">Copyright © 2020, All Rights Reserved</p>
</footer>

</body>
</html>
```